Wordpress template for a mens-choire webpage

Task is to design a Wordpress template for an 98 years old estonian mens choire webpage.
Design should involve details from the attached files, choire logo and the colors of the choire flag: in horizontal orientation bright sky-blue, white, bright grass-green.
Designer signature is allowed to be added to the template, with country of origin.

Reason: Deadline extended 2 days (until 2. March 2014) to accommodate designers creativity.

Thank you everyone for your great designs!
Our project has now entered into a voting and decision phase until 14th of March 2014 (included).

```html
<!DOCTYPE html>
<html lang="en">
<head>
<meta charset="utf-8">
<title>Valge Lind Meeskoor</title>
<link href="https://fonts.googleapis.com/css2?family=Ubuntu:wght@400;500&display=swap" rel="stylesheet">
<style>
:root{
  --sky:#1f6bb0;
  --grass:#3f6b1b;
  --red:#8e1010;
  --red-dark:#6a0808;
  --red-light:#a81a1a;
  --ink:#2a2a2a;
  --text:#444;
  --rule:#d6d6d6;
  --gold:#d4a43a;
}
*{box-sizing:border-box;margin:0;padding:0}
html,body{width:1200px;height:1149px;overflow:hidden}
body{position:relative;font-family:"Ubuntu",sans-serif;background:var(--sky);color:var(--text)}
.abs{position:absolute}
.header{left:0;top:0;width:1200px;height:94px;background:#fff}
.band-green{left:0;top:94px;width:1200px;height:239px;background:var(--grass)}
.page{left:150px;top:94px;width:900px;height:1055px;background:#fff}
.brand{left:210px;top:24px;display:flex;align-items:center;gap:8px}
.brand-mark{width:44px;height:44px;border-radius:50%;background:var(--red)}
.brand-name{font-size:17px;font-weight:500;color:var(--red)}
.lang{left:840px;top:26px;font-size:11px;color:#b00;font-weight:500}
.flag{left:910px;top:16px;width:35px;height:22px;border:1px solid #999}
.flag span{display:block;height:33.33%}
.search{left:768px;top:54px;width:239px;height:21px;display:flex}
.search .ico{width:22px;height:21px;background:#eee;border:1px solid #ccc;display:flex;align-items:center;justify-content:center}
.search .field{flex:1;margin-left:3px;border:1px solid #ccc;background:linear-gradient(#f4f4f4,#fff);font-size:11px;color:#555;padding:3px 5px}
.search .go{width:25px;margin-left:5px;background:linear-gradient(#ddd,#bbb);border-radius:3px;display:flex;align-items:center;justify-content:center}
.nav{left:150px;top:94px;width:900px;height:35px;background:linear-gradient(var(--red-light),var(--red-dark))}
.nav a{position:absolute;top:0;line-height:35px;font-size:11px;color:#fff;text-decoration:none;transform:translateX(-50%)}
.nav i{position:absolute;top:0;width:1px;height:35px;background:#c8403f}
.slider{left:150px;top:142px;width:900px;height:296px;background:linear-gradient(160deg,#8a857d,#5d5750 40%,#3a2a2a 70%,#9aa0a6)}
.caption{left:757px;top:156px;width:293px;height:30px;background:rgba(110,110,110,.8);color:#fff;font-size:19px;line-height:30px;padding-left:14px}
.bump{left:526px;top:412px;width:148px;height:40px;background:#fff;border-radius:74px 74px 0 0}
.dots{left:560px;top:423px;display:flex;gap:6px}
.dots span{width:8px;height:8px;border-radius:50%;background:#ddd;border:1px solid #888}
.dots span.on{background:#555}
.h2{font-size:18px;color:var(--ink);letter-spacing:.5px}
.rule{height:1px;background:var(--rule)}
.arrow{width:19px;height:19px;border-radius:50%;background:#bbb;display:flex;align-items:center;justify-content:center}
.thumb{width:189px;height:89px;border:1px solid #ccc}
.p-text{width:200px;font-size:10.3px;line-height:16px;color:#555;letter-spacing:-.1px}
.btn{width:86px;height:26px;background:linear-gradient(var(--red-light),var(--red-dark));border-radius:3px;color:#fff;font-size:12px;text-align:center;line-height:26px;box-shadow:0 1px 2px #888}
.small-thumb{width:67px;height:67px;border:2px solid #ddd}
.new-text{width:168px;font-size:9.6px;line-height:14px;text-align:justify;color:#444}
.welcome-img{left:471px;top:792px;width:258px;height:132px;border:1px solid #bbb;background:linear-gradient(#8f959b,#c9cdd0 55%,#9b958b)}
.welcome-text{left:471px;top:935px;width:258px;font-size:10px;line-height:17px;text-align:justify}
.date{width:61px;height:57px;background:var(--gold);color:#fff;text-align:center;font-size:18px;line-height:20px;padding-top:2px}
.date b{display:block;margin:3px auto 0;width:40px;height:25px;background:#fff;color:#555;border-radius:5px;font-weight:400;font-size:19px;line-height:25px}
.news-text{width:140px;font-size:10px;line-height:12.5px;color:#444}
.footer{left:150px;top:1076px;width:900px;height:73px;background:linear-gradient(#2c2c2c,#4a4a4a)}
.foot-links{left:198px;top:1092px;font-size:10.5px;color:#fff;font-weight:500;word-spacing:2px}
.copy{left:197px;top:1118px;font-size:10px;color:#ddd}
.social{top:1099px;width:17px;height:17px;border-radius:3px}
</style>
</head>
<body>
<div class="abs header"></div>
<div class="abs band-green"></div>
<div class="abs page"></div>

<div class="abs brand"><span class="brand-mark"></span><span class="brand-name">Valge Lind</span></div>
<div class="abs lang">ESTONIAN</div>
<div class="abs flag"><span style="background:#0072ce"></span><span style="background:#000"></span><span style="background:#fff"></span></div>
<div class="abs search">
  <span class="ico"><svg width="12" height="12" viewBox="0 0 12 12"><circle cx="5" cy="5" r="3.6" fill="none" stroke="#222" stroke-width="1.6"/><line x1="7.6" y1="7.6" x2="11" y2="11" stroke="#222" stroke-width="1.8"/></svg></span>
  <span class="field">Search</span>
  <span class="go"><svg width="11" height="10" viewBox="0 0 11 10"><path d="M0 4h6V1l5 4-5 4V6H0z" fill="#333"/></svg></span>
</div>

<nav class="abs nav">
  <a style="left:78px">HOME</a><i style="left:119px"></i>
  <a style="left:157px">ABOUT US</a><i style="left:200px"></i>
  <a style="left:250px">SERVICES</a><i style="left:282px"></i>
  <a style="left:319px">BLOG</a><i style="left:363px"></i>
  <a style="left:403px">GALLERY</a><i style="left:445px"></i>
  <a style="left:487px">CONTACT</a>
</nav>

<div class="abs slider" role="img" aria-label="Choir men in traditional black coats standing in front of an old stone ruin"></div>
<div class="abs caption">98 Years of Estonian Choire</div>
<div class="abs bump"></div>
<div class="abs dots"><span></span><span class="on"></span><span></span><span></span><span></span><span></span></div>

<div class="abs h2" style="left:195px;top:454px">Latest Projects</div>
<div class="abs arrow" style="left:959px;top:456px"><svg width="8" height="10"><path d="M6 1L2 5l4 4" stroke="#fff" stroke-width="2" fill="none"/></svg></div>
<div class="abs arrow" style="left:986px;top:456px"><svg width="8" height="10"><path d="M2 1l4 4-4 4" stroke="#fff" stroke-width="2" fill="none"/></svg></div>
<div class="abs rule" style="left:188px;top:481px;width:823px"></div>

<div class="abs thumb" style="left:195px;top:511px;background:linear-gradient(#3a3038,#6a4a40 60%,#b89a80)" role="img" aria-label="Choir performing on an outdoor stage before a crowd"></div>
<div class="abs thumb" style="left:401px;top:511px;background:linear-gradient(#c8c8c4,#8a2a30 55%,#b4b0aa)" role="img" aria-label="Choir in red jackets on a city square"></div>
<div class="abs thumb" style="left:608px;top:511px;background:linear-gradient(#6a4a30,#2a2420 55%,#7a5a40)" role="img" aria-label="Choir with orchestra in a concert hall"></div>
<div class="abs thumb" style="left:814px;top:511px;background:linear-gradient(#8a6a5a,#4a2e24 55%,#6a4434)" role="img" aria-label="Choir standing among church pews"></div>

<div class="abs p-text" style="left:195px;top:614px">Simply dummy text of the printing and typesetting industry.</div>
<div class="abs p-text" style="left:401px;top:614px">Simply dummy text of the printing and typesetting industry.</div>
<div class="abs p-text" style="left:608px;top:614px">Simply dummy text of the printing and typesetting industry.</div>
<div class="abs p-text" style="left:823px;top:614px">Simply dummy text of the printing and typesetting industry.</div>

<div class="abs btn" style="left:194px;top:663px">Read More</div>
<div class="abs btn" style="left:397px;top:662px">Read More</div>
<div class="abs btn" style="left:606px;top:662px">Read More</div>
<div class="abs btn" style="left:813px;top:662px">Read More</div>

<div class="abs rule" style="left:188px;top:734px;width:823px"></div>

<div class="abs h2" style="left:196px;top:760px">What’s New</div>
<div class="abs h2" style="left:471px;top:760px">Welcome</div>
<div class="abs h2" style="left:806px;top:760px">Latest News</div>

<div class="abs small-thumb" style="left:189px;top:799px;background:linear-gradient(#4a5a40,#2e3a2a)" role="img" aria-label="Portrait in a forest"></div>
<div class="abs small-thumb" style="left:189px;top:878px;background:linear-gradient(#9a8a70,#5a4a38)" role="img" aria-label="Figure beside a tree"></div>
<div class="abs small-thumb" style="left:189px;top:958px;background:linear-gradient(#4a5238,#303826)" role="img" aria-label="Portrait in greenery"></div>
<div class="abs new-text" style="left:275px;top:801px">Decently interviewed by Harbor Weekly who had seen her work on seating position in meetings.</div>
<div class="abs new-text" style="left:275px;top:879px">Minus quod maxime placeat dolor facere possimus voluptas facere possimus voluptas assumenda est omnis [...]</div>
<div class="abs new-text" style="left:274px;top:959px">Omnis dolor repellendus aut aut temporibus quibdam aut officiis debitis temporibus quibdam aut officiis debitis [...]</div>

<div class="abs welcome-img" role="img" aria-label="Choir in black suits standing in a line along a seaside pier"></div>
<div class="abs welcome-text">Lorem Ipsum is simply dummy text of the printing and typesetting industry lorem Ipsum has been the industry's standard dummy text ever since. the 1500s, when an unknown printer took a galley of type and scrambled.</div>

<div class="abs date" style="left:803px;top:806px">apr<b>28</b></div>
<div class="abs news-text" style="left:873px;top:807px">Lorem ipsum dolor sit amet, consectetuer adipiscing elit, sed diam nonummy nibh euismod tincidunt ut laoreet dolore magna aliquam erat</div>
<div class="abs date" style="left:803px;top:887px">may<b>23</b></div>
<div class="abs news-text" style="left:870px;top:888px">Lorem ipsum dolor sit amet, consectetuer adipiscing elit, sed diam nonummy nibh euismod tincidunt.</div>
<div class="abs date" style="left:803px;top:966px">july<b>19</b></div>
<div class="abs news-text" style="left:870px;top:967px">Lorem ipsum dolor sit amet, consectetuer adipiscing elit, sed diam nonummy nibh euismod tincidunt.</div>

<footer class="abs footer"></footer>
<div class="abs foot-links">HOME &nbsp;| &nbsp;ABOUT US &nbsp;| &nbsp;BLOG &nbsp;| &nbsp;SERVICES &nbsp;| &nbsp;GALLERY &nbsp;| &nbsp;CONTACT US</div>
<div class="abs copy">Copyright 2014 &nbsp;VALGE LIND MEESKOOR &nbsp;| All Rights Reserved</div>
<span class="abs social" style="left:896px;background:#4aa3df"></span>
<span class="abs social" style="left:921px;background:#3b5ea8"></span>
<span class="abs social" style="left:946px;background:#f08a24"></span>
<span class="abs social" style="left:970px;background:#5a9ad6"></span>
</body>
</html>
```